Hardcore nerd needs to stand out in a sea of dull Defence business cards

Wombarra Devices is a new Australian consulting engineering company that turns research and theory into practical systems. No evangelistic fluff, just mathematics and physics into electronic and optical circuits for consumer products, scientific research or Defence applications.

We already have a recognised logo (provided) which is often dark blue/black on a light background but we're open to other combinations. (Us engineers tend to have limited aesthetic imagination :)

Some of our recent products have included:
* Instrumentation for electrical testing,
* Radar jammers,
* GPS antenna design,
* Satellite tracking systems,
* High power lasers

We're open to both single and double-sided designs - happy to be convinced either way.

P.S. Another group is working on the web page, so - alas - our web site is currently of no use for images/ideas...

Target Market(s)

Engineering managers,
Scientists

Contact Information for Business Card

Dr Colin Harte
R&D Engineer

colin@wombarradevices.com.au
0427 563 710

PO Box XXX (to be confirmed)
Kelsby ACT 2917
Australia

Font styles to use
Serif
Sans Serif

Colors

Designer to choose colors to be used in the design.

Requirements
Must have
• My contact details!
• I've had many (great) "bold and plain" designs submitted already, so feel free to be artistically creative :)
• Happy to take advice re fonts/colours/printability etc.
Nice to have
• I'm not sure if "lists" are more at home on a CV than a business card, but representative services include:
• Applied electromagnetics
• RF and high speed electronics
• Signal and image processing
• Electro-optical and laser systems
• Concept-to-prototype design services
• If you're considering double sided cards, then often measuring/alignment grids/rulers feature on the back of similar cards.
• e.g. https://www.veltranoptics.example/newgrouppage9.cfm?objectgroup_id=4183
• https://www.veltranoptics.example/newgrouppage9.cfm?objectgroup_ID=4185
• ..or even a "Smith chart" (google will return lots)
• Generic images to represent a capability might work - googling images associated with keyword for each of these areas might help:
• - "passive radar", "phased array", "fdtd", "vircator"
• RF and high speed electronic design
• - "smith chart", "microstrip circuits", "dimensioned drawing", "electronic schematic"
• - "dft", "iir filter"
• - "optical cavity". "laser energy level diagram"
• Background/watermarked images outlines/wireframes/schematics would probably look OK.
Should not have
• If a list of projects/services is provided, it is important not to make the client feel that this is "all" the company can do. Engineering design is a creative discipline (like graphics :)
• Please, no stock "military" snaps like planes, missiles, etc!

```html
<!DOCTYPE html>
<html lang="en">
<head>
<meta charset="utf-8">
<title>Wombarra Devices – Business Card</title>
<link rel="stylesheet" href="https://fonts.googleapis.com/css2?family=Roboto:wght@400;700;900&display=swap">
<style>
  :root {
    --navy: #222a5e;
    --paper: #ffffff;
    --ink-grey: #6b6b70;
    --stage: #e7e8ec;
    --rule: #2b3370;
  }
  * { margin: 0; padding: 0; box-sizing: border-box; }
  html, body {
    width: 1200px; height: 913px; overflow: hidden;
    background: var(--stage);
    font-family: "Roboto", Arial, sans-serif;
  }
  .canvas { position: relative; width: 1200px; height: 913px; }

  .card {
    position: absolute;
    width: 540px; height: 310px;
    border-radius: 22px;
    box-shadow: 0 10px 28px rgba(20, 24, 50, 0.18);
    overflow: hidden;
  }

  /* front */
  .card--front { left: 70px; top: 90px; background: var(--navy); }
  .card--front .brand {
    position: absolute; left: 50%; top: 50%;
    transform: translate(-50%, -50%);
    display: flex; align-items: center; gap: 16px;
    color: var(--paper);
  }
  .brand__dot {
    width: 62px; height: 62px; border-radius: 50%;
    background: currentColor; flex: none;
  }
  .brand__name {
    font-weight: 900; font-size: 34px; line-height: 1;
    text-transform: uppercase; letter-spacing: 0.5px;
  }

  /* back */
  .card--back { left: 590px; top: 500px; background: var(--paper); }
  .card--back .brand {
    position: absolute; right: 36px; top: 40px;
    display: flex; align-items: center; gap: 10px;
    color: var(--navy);
  }
  .card--back .brand__dot { width: 40px; height: 40px; }
  .card--back .brand__name { font-size: 22px; }

  .rule { position: absolute; height: 1.5px; background: var(--rule); }
  .rule--top { right: 36px; top: 110px; width: 250px; }
  .rule--mid { left: 36px; top: 222px; width: 190px; }

  .person { position: absolute; left: 36px; top: 168px; }
  .person__name {
    color: var(--navy); font-weight: 900; font-size: 21px;
    text-transform: uppercase; letter-spacing: 0.2px;
  }
  .person__role { color: var(--ink-grey); font-size: 13px; margin-top: 2px; }

  .contacts {
    position: absolute; left: 36px; top: 234px;
    list-style: none; color: var(--ink-grey); font-size: 12.5px;
  }
  .contacts li { display: flex; align-items: center; gap: 8px; line-height: 20px; }
  .contacts svg { width: 11px; height: 11px; fill: var(--navy); flex: none; }

  .address {
    position: absolute; right: 36px; top: 150px;
    text-align: right; color: var(--ink-grey);
    font-size: 12.5px; line-height: 18px;
  }
</style>
</head>
<body>
<main class="canvas">

  <section class="card card--front" aria-label="Card front">
    <div class="brand">
      <span class="brand__dot"></span>
      <span class="brand__name">Wombarra Devices</span>
    </div>
  </section>

  <section class="card card--back" aria-label="Card back">
    <div class="brand">
      <span class="brand__dot"></span>
      <span class="brand__name">Wombarra Devices</span>
    </div>
    <div class="rule rule--top"></div>

    <address class="address" style="font-style:normal">
      PO Box XXX (to be confirmed)<br>
      Kelsby ACT 2917, Australia
    </address>

    <div class="person">
      <h1 class="person__name">Dr Colin Harte</h1>
      <p class="person__role">R&amp;D Engineer</p>
    </div>
    <div class="rule rule--mid"></div>

    <ul class="contacts">
      <li>
        <svg viewBox="0 0 24 24" aria-hidden="true"><path d="M6.6 10.8a15.1 15.1 0 0 0 6.6 6.6l2.2-2.2c.3-.3.7-.4 1-.2 1.1.4 2.3.6 3.6.6.6 0 1 .4 1 1V20c0 .6-.4 1-1 1C10.6 21 3 13.4 3 4c0-.6.4-1 1-1h3.5c.6 0 1 .4 1 1 0 1.3.2 2.5.6 3.6.1.3 0 .7-.2 1z"/></svg>
        0427 563 710
      </li>
      <li>
        <svg viewBox="0 0 24 24" aria-hidden="true"><path d="M2 5h20v14H2z M2 5l10 8 10-8" /></svg>
        colin@wombarradevices.com.au
      </li>
      <li>
        <svg viewBox="0 0 24 24" aria-hidden="true"><circle cx="12" cy="12" r="10"/></svg>
        www.wombarradevices.com.au
      </li>
    </ul>
  </section>

</main>
</body>
</html>
```